Power Generation Company needs a stationary design

We need a design for our letter envelope, A4 Envelope and letterhead. Our company name is VALTRENO Power which i attached here sample our our call card. We are based in the Philippines and is into the Power Generation business. We own power facilities like Hydropower plant, Solar Power Plant, Diesel Power Plant, Gas Turbine Power Plant. We sell our power to various electric distribution companies, factories and office buildings.

Target Market(s)

Electric Distribution Companies and Factories

Industry/Entity Type

It Company

Colors
ec1f27

Requirements
Must have
• Logo and company name
Nice to have
• No specific
Should not have
• No specific

```html
<!DOCTYPE html>
<html lang="en">
<head>
<meta charset="utf-8">
<title>VALTRENO Power Letterhead</title>
<link href="https://fonts.googleapis.com/css2?family=Open+Sans:wght@400;600;700&display=swap" rel="stylesheet">
<style>
  :root {
    --brand-red: #ec1f27;
    --ink: #4a4a4a;
    --steel-light: #e2e2e2;
    --paper: #ffffff;
    --backdrop: #eeb0a7;
  }
  html, body {
    margin: 0;
    padding: 0;
    width: 1200px;
    height: 784px;
    overflow: hidden;
    background: var(--backdrop);
    font-family: "Open Sans", Arial, sans-serif;
  }
  .letterhead {
    position: absolute;
    left: 338px;
    top: 22px;
    width: 523px;
    height: 740px;
    background: var(--paper);
    box-shadow: 0 6px 18px rgba(120, 50, 45, 0.25);
    overflow: hidden;
  }
  .corner-fold {
    position: absolute;
    left: 0;
    top: 0;
    width: 523px;
    height: 740px;
  }
  .edge-line {
    position: absolute;
    left: 0;
    bottom: 0;
    width: 100%;
    height: 3px;
    background: var(--brand-red);
  }
  .brand {
    position: absolute;
    left: 140px;
    top: 46px;
    display: flex;
    align-items: center;
    gap: 8px;
  }
  .brand-dot {
    width: 16px;
    height: 16px;
    border-radius: 50%;
    background: var(--brand-red);
  }
  .brand-name {
    font-weight: 700;
    font-size: 20px;
    letter-spacing: 1px;
    line-height: 1;
    color: var(--brand-red);
    white-space: nowrap;
  }
  .contact {
    position: absolute;
    left: 40px;
    top: 640px;
    width: 460px;
  }
  .contact-label {
    display: inline-block;
    padding: 3px 10px 3px 9px;
    background: var(--steel-light);
    border-left: 3px solid var(--brand-red);
    border-bottom: 2px solid var(--brand-red);
    font-size: 8px;
    font-weight: 700;
    color: var(--brand-red);
  }
  .contact-grid {
    position: absolute;
    top: 34px;
    left: 78px;
    display: flex;
    gap: 18px;
  }
  .contact-col {
    display: flex;
    flex-direction: column;
    gap: 5px;
  }
  .contact-item {
    display: flex;
    align-items: flex-start;
    gap: 5px;
    font-size: 7.5px;
    line-height: 11px;
    color: var(--ink);
    white-space: nowrap;
  }
  .contact-icon {
    flex: none;
    width: 10px;
    height: 10px;
    margin-top: 0.5px;
  }
</style>
</head>
<body>
  <main class="letterhead">
    <svg class="corner-fold" viewBox="0 0 523 740" aria-hidden="true">
      <defs>
        <linearGradient id="steelFade" x1="0" y1="0" x2="1" y2="0">
          <stop offset="0" stop-color="#9a9a9a"/>
          <stop offset="0.6" stop-color="#6f6f6f"/>
          <stop offset="1" stop-color="#5a5a5a"/>
        </linearGradient>
        <linearGradient id="redFade" x1="0" y1="0" x2="1" y2="1">
          <stop offset="0" stop-color="#ff3b3f"/>
          <stop offset="1" stop-color="#d9141b"/>
        </linearGradient>
      </defs>
      <polygon class="fold-steel" points="0,625 40,696 280,734 280,740 0,740" fill="url(#steelFade)"/>
      <polygon class="fold-red" points="0,548 0,625 40,696" fill="url(#redFade)"/>
    </svg>
    <div class="edge-line"></div>

    <header class="brand">
      <span class="brand-dot"></span>
      <span class="brand-name">VALTRENO Power</span>
    </header>

    <footer class="contact">
      <div class="contact-label">Contact Detail</div>
      <div class="contact-grid">
        <div class="contact-col">
          <div class="contact-item">
            <svg class="contact-icon" viewBox="0 0 10 10"><circle cx="5" cy="5" r="5" fill="#ec1f27"/><rect x="2.5" y="3.2" width="5" height="3.6" fill="none" stroke="#fff" stroke-width="0.7"/><polyline points="2.5,3.2 5,5.2 7.5,3.2" fill="none" stroke="#fff" stroke-width="0.7"/></svg>
            <span>info@valtreno-net.com</span>
          </div>
          <div class="contact-item">
            <svg class="contact-icon" viewBox="0 0 10 10"><circle cx="5" cy="5" r="5" fill="#ec1f27"/><circle cx="5" cy="5" r="2.6" fill="none" stroke="#fff" stroke-width="0.6"/><line x1="2.4" y1="5" x2="7.6" y2="5" stroke="#fff" stroke-width="0.6"/><ellipse cx="5" cy="5" rx="1.1" ry="2.6" fill="none" stroke="#fff" stroke-width="0.6"/></svg>
            <span>www.valtreno-net.com</span>
          </div>
        </div>
        <div class="contact-col">
          <div class="contact-item">
            <svg class="contact-icon" viewBox="0 0 10 10"><circle cx="5" cy="5" r="5" fill="#ec1f27"/><path d="M3 3.2c0-.4.3-.6.6-.6h.5l.6 1.4-.6.5c.3.7.8 1.2 1.5 1.5l.5-.6 1.4.6v.5c0 .3-.2.6-.6.6C4.8 7.1 3 5.3 3 3.2z" fill="#fff"/></svg>
            <span>+632 555 0140</span>
          </div>
          <div class="contact-item">
            <svg class="contact-icon" viewBox="0 0 10 10"><circle cx="5" cy="5" r="5" fill="#ec1f27"/><rect x="2.6" y="4" width="4.8" height="3" fill="#fff"/><rect x="3.6" y="2.6" width="2.8" height="1.6" fill="none" stroke="#fff" stroke-width="0.6"/></svg>
            <span>+632 555 0141</span>
          </div>
          <div class="contact-item">
            <svg class="contact-icon" viewBox="0 0 10 10"><circle cx="5" cy="5" r="5" fill="#ec1f27"/><rect x="3.5" y="2.3" width="3" height="5.4" rx="0.5" fill="none" stroke="#fff" stroke-width="0.7"/><circle cx="5" cy="6.6" r="0.35" fill="#fff"/></svg>
            <span>+63 900 555 0142</span>
          </div>
        </div>
        <div class="contact-col">
          <div class="contact-item">
            <svg class="contact-icon" viewBox="0 0 10 10"><circle cx="5" cy="5" r="5" fill="#ec1f27"/><path d="M5 2.2a1.9 1.9 0 0 1 1.9 1.9C6.9 5.5 5 7.8 5 7.8S3.1 5.5 3.1 4.1A1.9 1.9 0 0 1 5 2.2z" fill="#fff"/><circle cx="5" cy="4.1" r="0.7" fill="#ec1f27"/></svg>
            <span>88 Meridian Business Tower, 450 Narra Ave.<br>Lakeview Business Park, Lakeview,<br>Sta. Rosa, Laguna, 4026 Philippines</span>
          </div>
        </div>
      </div>
    </footer>
  </main>
</body>
</html>
```